Linkora Banner Design for B2B Consulting Firm

Take the already developed logo (attached) and incorporate it into a creative banner design for placement on Linkora (the social media platform targeting business users). The banner will be used on the firm's company profile page on Linkora (not yet created).

```html
<!DOCTYPE html>
<html lang="en">
<head>
<meta charset="utf-8">
<title>Corporate Fractional Marketing Services – Profile Banner Presentation</title>
<link rel="stylesheet" href="https://fonts.googleapis.com/css2?family=Poppins:wght@300;700;800&family=Roboto:wght@400;500;700&display=swap">
<style>
  :root {
    --stage-top: #888a88;
    --stage-bottom: #555555;
    --screen-bg: #f2f1ee;
    --card-bg: #ffffff;
    --card-line: #dcdcdc;
    --ink: #1d1d1d;
    --ink-soft: #555555;
    --ink-muted: #8a8a8a;
    --icon: #5f5f5f;
    --action-blue: #2a7ae2;
    --search-bg: #d0d0d0;
    --ad-slot: #ececec;
    --brand-green: #587a5e;
    --haze-green: #d7ddd6;
    --haze-grey: #e4e7e3;
    --ring-blue: #d3e4ec;
    --globe-blue: #7ccbeb;
    --globe-deep: #3fa9dd;
  }
  * { margin: 0; padding: 0; box-sizing: border-box; }
  html, body {
    width: 1040px;
    height: 1200px;
    overflow: hidden;
    background: var(--stage-bottom);
    font-family: 'Roboto', sans-serif;
  }
  .canvas { position: relative; width: 1040px; height: 1200px; }
  .stage-top {
    position: absolute; left: 0; top: 0; width: 1040px; height: 638px;
    background: var(--stage-top);
  }

  /* ---------- profile screen ---------- */
  .screen {
    position: absolute; left: 51px; top: 109px; width: 938px; height: 437px;
    background: var(--screen-bg);
    border-radius: 12px 12px 0 0;
    overflow: hidden;
  }
  .screen > * { position: absolute; }
  .network-name {
    left: 52px; top: 30px; height: 40px; line-height: 40px;
    font-weight: 700; font-size: 15px; color: var(--action-blue);
  }
  .search {
    left: 108px; top: 30px; width: 233px; height: 40px;
    background: var(--search-bg); border-radius: 6px;
    display: flex; align-items: center; gap: 10px; padding-left: 17px;
    font-size: 14px; color: #5a5a5a;
  }
  .nav-icon { top: 38px; width: 26px; height: 26px; }
  .nav-active { left: 477px; top: 71px; width: 36px; height: 2px; background: #444; }

  .profile-card {
    left: 50px; top: 83px; width: 632px; height: 277px;
    background: var(--card-bg); border: 1px solid var(--card-line); border-radius: 8px;
    overflow: hidden;
  }
  .profile-card .banner {
    position: absolute; left: 0; top: 11px;
    transform: scale(0.69); transform-origin: 0 0;
  }
  .company-mark {
    left: 86px; top: 148px; width: 72px; height: 72px;
    background: var(--card-bg); border: 2px solid var(--brand-green);
    display: flex; align-items: center; justify-content: center; text-align: center;
    font-family: 'Poppins', sans-serif; font-weight: 300; font-size: 10px; line-height: 13px;
    color: var(--brand-green);
  }
  .company-name { left: 84px; top: 224px; font-size: 21px; font-weight: 700; color: var(--ink); }
  .company-meta { left: 84px; top: 253px; font-size: 9px; color: var(--ink-soft); }
  .company-staff { left: 84px; top: 267px; font-size: 12px; color: var(--ink); }
  .actions { left: 81px; top: 292px; display: flex; gap: 8px; }
  .btn {
    height: 23px; border-radius: 12px; font-size: 10px; font-weight: 500;
    display: flex; align-items: center; justify-content: center;
  }
  .btn--primary { width: 71px; background: var(--action-blue); color: #fff; }
  .btn--outline { width: 90px; border: 1px solid var(--action-blue); color: var(--action-blue); }
  .btn--muted { width: 61px; border: 1px solid #666; color: #333; }
  .divider { left: 52px; top: 326px; width: 628px; height: 1px; background: var(--card-line); }
  .tabs { left: 84px; top: 335px; display: flex; font-size: 12px; font-weight: 500; color: #333; }
  .tabs span { margin-right: 30px; }
  .tabs .is-current { color: var(--ink); }
  .tab-underline { left: 84px; top: 351px; width: 34px; height: 2px; background: var(--ink); }

  .about-card {
    left: 52px; top: 367px; width: 628px; height: 90px;
    background: var(--card-bg); border: 1px solid var(--card-line); border-radius: 8px;
  }
  .about-title { left: 84px; top: 377px; font-size: 12.5px; font-weight: 500; color: var(--ink); }
  .about-text { left: 83px; top: 396px; width: 540px; font-size: 8px; line-height: 12.6px; color: #333; }

  .ads-card {
    left: 692px; top: 86px; width: 200px; height: 153px;
    background: var(--card-bg); border: 1px solid var(--card-line); border-radius: 8px;
  }
  .ads-label { left: 713px; top: 95px; font-size: 9.5px; font-weight: 500; color: var(--ink-soft); }
  .ads-more { left: 853px; top: 90px; font-size: 11px; letter-spacing: 1px; color: var(--ink-soft); }
  .ads-slot { left: 712px; top: 114px; width: 160px; height: 110px; background: var(--ad-slot); border-radius: 8px; }

  .feed-card {
    left: 692px; top: 247px; width: 200px; height: 220px;
    background: var(--card-bg); border: 1px solid var(--card-line); border-radius: 8px;
  }
  .feed-title { left: 710px; top: 262px; font-size: 12.5px; font-weight: 500; color: var(--ink); }
  .avatar { width: 40px; height: 40px; }
  .feed-name { left: 757px; font-size: 14.5px; font-weight: 500; color: #333; }
  .feed-sector { left: 757px; font-size: 10px; font-weight: 500; color: #333; }
  .feed-count { left: 757px; font-size: 8.5px; color: var(--ink-muted); }
  .feed-follow {
    left: 757px; top: 343px; width: 84px; height: 26px; border-radius: 13px;
    background: var(--action-blue); color: #fff; font-size: 12.5px; font-weight: 500;
    display: flex; align-items: center; justify-content: center; gap: 8px;
  }

  /* ---------- banner ---------- */
  .banner {
    position: absolute; width: 917px; height: 155px; overflow: hidden;
    background: #ffffff;
  }
  .banner--flat { left: 62px; top: 795px; }
  .banner__crowd {
    position: absolute; left: 0; top: 0; width: 300px; height: 100%;
    background: linear-gradient(90deg, var(--haze-green) 0%, var(--haze-grey) 50%, rgba(255,255,255,0) 100%);
  }
  .banner__skyline {
    position: absolute; right: 0; top: 0; width: 370px; height: 100%;
    background: linear-gradient(270deg, var(--haze-green) 0%, var(--haze-grey) 55%, rgba(255,255,255,0) 100%);
  }
  .banner__headline {
    position: absolute; left: 260px; top: 32px;
    font-family: 'Poppins', sans-serif; color: var(--brand-green);
  }
  .banner__kicker { display: block; font-weight: 300; font-size: 30px; line-height: 30px; }
  .banner__service { display: block; font-weight: 800; font-size: 31px; line-height: 29px; letter-spacing: -0.3px; }
  .banner__emblem { position: absolute; left: 727px; top: -15px; width: 180px; height: 180px; }
</style>
</head>
<body>
<main class="canvas">
  <div class="stage-top"></div>

  <section class="screen" aria-label="Company profile page preview">
    <div class="network-name">Linkora</div>
    <div class="search">
      <svg width="18" height="18" viewBox="0 0 18 18"><circle cx="7.5" cy="7.5" r="5.5" fill="none" stroke="#555" stroke-width="2"/><line x1="11.5" y1="11.5" x2="16" y2="16" stroke="#555" stroke-width="2" stroke-linecap="round"/></svg>
      <span>Search</span>
    </div>

    <svg class="nav-icon" style="left:482px" viewBox="0 0 26 26"><path d="M13 3 L24 12 H21 V23 H16 V16 H10 V23 H5 V12 H2 Z" fill="var(--icon)"/></svg>
    <svg class="nav-icon" style="left:553px" viewBox="0 0 26 26"><circle cx="9" cy="7" r="4" fill="var(--icon)"/><rect x="4" y="12" width="10" height="12" rx="3" fill="var(--icon)"/><circle cx="19" cy="13" r="3" fill="var(--icon)"/><rect x="15.5" y="17" width="7" height="7" rx="2" fill="var(--icon)"/></svg>
    <svg class="nav-icon" style="left:620px" viewBox="0 0 26 26"><rect x="9" y="3" width="8" height="5" rx="1.5" fill="none" stroke="var(--icon)" stroke-width="2"/><rect x="1" y="7" width="24" height="16" rx="3" fill="var(--icon)"/><line x1="1" y1="15" x2="25" y2="15" stroke="#f2f1ee" stroke-width="1.5"/></svg>
    <svg class="nav-icon" style="left:684px" viewBox="0 0 26 26"><path d="M13 3 C20 3 25 7 25 12 C25 17 20 20 13 20 L6 24 L7 19 C3 17 1 15 1 12 C1 7 6 3 13 3 Z" fill="var(--icon)"/><circle cx="8" cy="12" r="1.6" fill="#fff"/><circle cx="13" cy="12" r="1.6" fill="#fff"/><circle cx="18" cy="12" r="1.6" fill="#fff"/></svg>
    <svg class="nav-icon" style="left:744px" viewBox="0 0 26 26"><path d="M13 2 C18 2 20 6 20 11 V16 L23 19 H3 L6 16 V11 C6 6 8 2 13 2 Z" fill="var(--icon)"/><rect x="10" y="20" width="6" height="4" rx="2" fill="var(--icon)"/></svg>
    <svg class="nav-icon" style="left:804px" viewBox="0 0 26 26"><circle cx="13" cy="13" r="12" fill="var(--icon)"/><circle cx="13" cy="10" r="4.5" fill="#fff"/><path d="M5 21 C7 16 19 16 21 21 C18 24 8 24 5 21 Z" fill="#fff"/></svg>
    <svg class="nav-icon" style="left:861px" viewBox="0 0 26 26"><g fill="var(--icon)"><circle cx="5" cy="5" r="2"/><circle cx="13" cy="5" r="2"/><circle cx="21" cy="5" r="2"/><circle cx="5" cy="13" r="2"/><circle cx="13" cy="13" r="2"/><circle cx="21" cy="13" r="2"/><circle cx="5" cy="21" r="2"/><circle cx="13" cy="21" r="2"/><circle cx="21" cy="21" r="2"/></g></svg>
    <div class="nav-active"></div>

    <div class="profile-card">
      <div class="banner" aria-label="Profile cover banner">
        <div class="banner__crowd" role="img" aria-label="Faded photo of business people in front of a city skyline"></div>
        <div class="banner__skyline" role="img" aria-label="Faded city skyline with a data gauge"></div>
        <div class="banner__headline">
          <span class="banner__kicker">BEST-IN-CLASS</span>
          <span class="banner__service">CORPORATE FRACTIONAL</span>
          <span class="banner__service">MARKETING SERVICES</span>
        </div>
        <svg class="banner__emblem" viewBox="0 0 180 180" role="img" aria-label="Business handshake over a glowing globe">
          <defs>
            <radialGradient id="globeFillSmall" cx="50%" cy="45%" r="55%">
              <stop offset="0%" stop-color="#b9e6f7"/><stop offset="60%" stop-color="#7ccbeb"/><stop offset="100%" stop-color="#3fa9dd"/>
            </radialGradient>
          </defs>
          <circle cx="90" cy="90" r="90" fill="#d3e4ec"/>
          <circle cx="90" cy="90" r="75" fill="url(#globeFillSmall)"/>
        </svg>
      </div>
    </div>

    <div class="company-mark">Fernhill<br>Advisors</div>
    <div class="company-name">The Company</div>
    <div class="company-meta">Commercial Real Estate · 6.762 followers</div>
    <div class="company-staff">See all 1.239 employees in Linkora</div>
    <div class="actions">
      <span class="btn btn--primary">Follow</span>
      <span class="btn btn--outline">Visit website</span>
      <span class="btn btn--muted">More</span>
    </div>
    <div class="divider"></div>
    <nav class="tabs"><span class="is-current">Home</span><span>About</span><span>Posts</span><span>Jobs</span><span>People</span></nav>
    <div class="tab-underline"></div>

    <div class="about-card"></div>
    <div class="about-title">About</div>
    <p class="about-text">Lorem ipsum dolor sit amet, consectetuer adipiscing elit, sed diam nonummy nibh euismod tincidunt ut laoreet dolore magna aliquam erat volutpat. Ut wisi enim ad minim veniam, quis nostrud exerci tation ullamcorper suscipit lobortis nisl ut aliquip ex ea commodo consequat. Duis autem vel eum iriure dolor in hendrerit in vulputate velit esse molestie consequat.</p>

    <div class="ads-card"></div>
    <div class="ads-label">Ads</div>
    <div class="ads-more">···</div>
    <div class="ads-slot"></div>

    <div class="feed-card"></div>
    <div class="feed-title">Add to your feed</div>
    <svg class="avatar" style="left:710px; top:294px" viewBox="0 0 40 40"><circle cx="20" cy="20" r="20" fill="#4a4a4a"/><circle cx="20" cy="15" r="7" fill="#fff"/><path d="M7 33 C10 24 30 24 33 33 C28 38 12 38 7 33 Z" fill="#fff"/></svg>
    <div class="feed-name" style="top:291px">The Company</div>
    <div class="feed-sector" style="top:309px">Real Estate</div>
    <div class="feed-count" style="top:323px">78.292 Followers</div>
    <div class="feed-follow"><span>+</span><span>Follow</span></div>
    <svg class="avatar" style="left:710px; top:392px" viewBox="0 0 40 40"><circle cx="20" cy="20" r="20" fill="#4a4a4a"/><circle cx="20" cy="15" r="7" fill="#fff"/><path d="M7 33 C10 24 30 24 33 33 C28 38 12 38 7 33 Z" fill="#fff"/></svg>
    <div class="feed-name" style="top:389px">The Company</div>
    <div class="feed-sector" style="top:408px">Digital Agency</div>
    <div class="feed-count" style="top:423px">108.273 Followers</div>
  </section>

  <section class="banner banner--flat" aria-label="Profile cover banner">
    <div class="banner__crowd" role="img" aria-label="Faded photo of business people in front of a city skyline"></div>
    <div class="banner__skyline" role="img" aria-label="Faded city skyline with a data gauge"></div>
    <h1 class="banner__headline">
      <span class="banner__kicker">BEST-IN-CLASS</span>
      <span class="banner__service">CORPORATE FRACTIONAL</span>
      <span class="banner__service">MARKETING SERVICES</span>
    </h1>
    <svg class="banner__emblem" viewBox="0 0 180 180" role="img" aria-label="Business handshake over a glowing globe">
      <defs>
        <radialGradient id="globeFill" cx="50%" cy="45%" r="55%">
          <stop offset="0%" stop-color="#b9e6f7"/><stop offset="60%" stop-color="#7ccbeb"/><stop offset="100%" stop-color="#3fa9dd"/>
        </radialGradient>
      </defs>
      <circle cx="90" cy="90" r="90" fill="#d3e4ec"/>
      <circle cx="90" cy="90" r="75" fill="url(#globeFill)"/>
    </svg>
  </section>
</main>
</body>
</html>
```